Copper Hollow Mini Storage - Ad for half Page

Need half page ad for a publication.
would also like to be able to use in the future
self storage facility - 3 locations, the third opening soon
do not like real busy projects...i have a logo but willing to tweak if needed

```html
<!DOCTYPE html>
<html lang="en">
<head>
<meta charset="utf-8">
<title>Copper Hollow Mini Storage – Half Page Ad</title>
<link rel="stylesheet" href="https://fonts.googleapis.com/css2?family=Anton&family=Montserrat:wght@400;600;700;800&family=Oswald:wght@500;600&display=swap">
<style>
  :root {
    --ink: #2a2526;
    --copper: #a0622a;
    --copper-dark: #8a5222;
    --rust: #7a3a26;
    --grey-text: #262626;
    --paper: #ffffff;
    --stage: #d9d9d9;
  }
  * { box-sizing: border-box; margin: 0; padding: 0; }
  html, body { width: 873px; height: 1200px; overflow: hidden; background: var(--stage); }
  .ad {
    position: absolute; left: 20px; top: 322px;
    width: 1512px; height: 1010px;
    transform: scale(0.5509); transform-origin: 0 0;
    background: var(--paper);
    box-shadow: 0 6px 20px rgba(0,0,0,.25);
    overflow: hidden;
    font-family: "Montserrat", sans-serif;
  }
  .ad > * { position: absolute; }
  .photo {
    left: 0; top: 0; width: 1512px; height: 878px;
    clip-path: polygon(815px 0, 1512px 0, 1512px 878px, 780px 878px, 885px 688px, 790px 526px, 645px 233px);
    background: linear-gradient(180deg, #86a9da 0%, #c7d6ea 30%, #e4e6e8 45%, #a9a49a 58%, #8d8a82 70%, #6f8a45 82%, #56722f 100%);
  }
  .panels { left: 0; top: 0; width: 1512px; height: 1010px; }

  .brand { left: 45px; top: 62px; display: flex; align-items: center; gap: 26px; }
  .brand-mark { width: 108px; height: 108px; background: var(--copper); }
  .brand-name { color: var(--paper); font-weight: 700; font-size: 54px; line-height: 1.05; letter-spacing: 1px; }

  .headline {
    left: 30px; top: 252px; color: var(--paper);
    font-family: "Oswald", sans-serif; font-weight: 600; font-size: 60px; line-height: 66px;
    text-shadow: 2px 2px 3px rgba(0,0,0,.35);
  }
  .intro { left: 30px; top: 405px; width: 670px; color: var(--paper); font-size: 20.5px; line-height: 29px; }

  .feature { top: 548px; display: flex; align-items: center; gap: 32px; }
  .feature.climate { left: 35px; }
  .feature.non-climate { left: 458px; }
  .feature-icon { width: 112px; height: 112px; background: var(--copper-dark); border-radius: 4px; display: grid; place-items: center; }
  .feature-label { color: var(--paper); font-weight: 700; font-size: 32px; line-height: 32px; }

  .perks { top: 712px; list-style: none; color: var(--paper); font-weight: 600; font-size: 23px; }
  .perks.left { left: 35px; }
  .perks.right { left: 448px; }
  .perks li { display: flex; align-items: center; gap: 22px; height: 34px; margin-bottom: 2px; }

  .launch { right: 52px; top: 55px; text-align: right; }
  .launch-title { font-family: "Anton", sans-serif; font-size: 112px; line-height: 118px; color: var(--ink); letter-spacing: -1px; }
  .launch-site { font-weight: 800; font-size: 54px; line-height: 60px; color: var(--copper); }

  .locations { right: 82px; top: 676px; text-align: right; font-family: "Oswald", sans-serif; font-weight: 600; line-height: 56px; }
  .locations-title { color: var(--rust); font-size: 42px; }
  .locations-line { color: var(--grey-text); font-size: 42px; }

  .contact { left: 35px; top: 912px; display: flex; align-items: center; font-family: "Oswald", sans-serif; font-weight: 500; font-size: 44px; color: var(--rust); }
  .contact .divider { color: var(--rust); margin: 0 26px 0 38px; font-weight: 600; }
  .contact svg { margin-right: 16px; }
</style>
</head>
<body>
<article class="ad">
  <div class="photo" role="img" aria-label="Photo of the new storage facility office building with climate control units, driveway and lawn under a blue sky"></div>

  <svg class="panels" width="1512" height="1010" viewBox="0 0 1512 1010" aria-hidden="true">
    <defs>
      <linearGradient id="greyPanel" x1="0" y1="0" x2="1" y2="0">
        <stop offset="0" stop-color="#9c9c9c"/>
        <stop offset=".55" stop-color="#e6e6e6"/>
        <stop offset="1" stop-color="#b3b3b3"/>
      </linearGradient>
    </defs>
    <polygon points="0,0 815,0 645,233 0,233" fill="var(--ink)"/>
    <polygon points="0,233 645,233 790,526 0,526" fill="var(--copper)"/>
    <polygon points="0,526 790,526 870,688 0,688" fill="var(--ink)"/>
    <polygon points="0,688 885,688 780,878 0,878" fill="var(--copper)"/>
    <polygon points="930,645 1512,645 1512,765 1452,878 780,878 885,688" fill="url(#greyPanel)"/>
    <polyline points="820,0 650,233 795,526 875,688 885,688" fill="none" stroke="#fff" stroke-width="7"/>
  </svg>

  <div class="brand">
    <div class="brand-mark"></div>
    <div class="brand-name">Copper Hollow<br>Mini Storage</div>
  </div>

  <h1 class="headline">HOW CAN I EMAIL OR<br>SEND A PIC OF AN AD I LIKE?</h1>
  <p class="intro">We are a family-owned, premier self-storage facility located in Riverton and Oak Falls. We offer solutions to your Personal Storage, Business Storage and RV &amp; Boat Storage needs.</p>

  <div class="feature climate">
    <div class="feature-icon">
      <svg width="80" height="80" viewBox="0 0 80 80" fill="none" stroke="#e9a45a" stroke-width="5" stroke-linecap="round">
        <path d="M40 12 a7 7 0 0 1 7 7 v30 a13 13 0 1 1 -14 0 v-30 a7 7 0 0 1 7 -7z"/>
        <line x1="40" y1="30" x2="40" y2="56"/>
        <line x1="18" y1="26" x2="26" y2="26"/><line x1="18" y1="36" x2="26" y2="36"/><line x1="18" y1="46" x2="26" y2="46"/>
        <path d="M56 22 a8 8 0 0 1 0 12"/><path d="M62 16 a16 16 0 0 1 0 24"/>
      </svg>
    </div>
    <div class="feature-label">CLIMATE<br>CONTROLLED<br>UNITS</div>
  </div>

  <div class="feature non-climate">
    <div class="feature-icon">
      <svg width="80" height="80" viewBox="0 0 80 80">
        <circle cx="44" cy="32" r="13" fill="#e9a45a"/>
        <path d="M18 62 a12 12 0 0 1 6 -22 a14 14 0 0 1 26 -2 a11 11 0 0 1 12 24z" fill="#e9a45a"/>
        <line x1="12" y1="70" x2="66" y2="10" stroke="#2a2526" stroke-width="4" stroke-linecap="round"/>
      </svg>
    </div>
    <div class="feature-label">NON<br>CLIMATE<br>UNITS</div>
  </div>

  <ul class="perks left">
    <li><svg width="20" height="20" viewBox="0 0 20 20" fill="none" stroke="#fff" stroke-width="2"><rect x="1" y="3" width="16" height="16"/><path d="M5 10l4 4 9-12"/></svg>Safe &amp; Secure units</li>
    <li><svg width="20" height="20" viewBox="0 0 20 20" fill="none" stroke="#fff" stroke-width="2"><rect x="1" y="3" width="16" height="16"/><path d="M5 10l4 4 9-12"/></svg>Friendly &amp; professional staff</li>
    <li><svg width="20" height="20" viewBox="0 0 20 20" fill="none" stroke="#fff" stroke-width="2"><rect x="1" y="3" width="16" height="16"/><path d="M5 10l4 4 9-12"/></svg>Electronic gate access</li>
    <li><svg width="20" height="20" viewBox="0 0 20 20" fill="none" stroke="#fff" stroke-width="2"><rect x="1" y="3" width="16" height="16"/><path d="M5 10l4 4 9-12"/></svg>Online account access</li>
  </ul>
  <ul class="perks right">
    <li><svg width="20" height="20" viewBox="0 0 20 20" fill="none" stroke="#fff" stroke-width="2"><rect x="1" y="3" width="16" height="16"/><path d="M5 10l4 4 9-12"/></svg>No deposit required</li>
    <li><svg width="20" height="20" viewBox="0 0 20 20" fill="none" stroke="#fff" stroke-width="2"><rect x="1" y="3" width="16" height="16"/><path d="M5 10l4 4 9-12"/></svg>Month-to-month rentals</li>
    <li><svg width="20" height="20" viewBox="0 0 20 20" fill="none" stroke="#fff" stroke-width="2"><rect x="1" y="3" width="16" height="16"/><path d="M5 10l4 4 9-12"/></svg>Security camera monitoring</li>
  </ul>

  <div class="launch">
    <div class="launch-title">COMING SOON!</div>
    <div class="launch-site">ELM GROVE @ RT 9</div>
  </div>

  <div class="locations">
    <div class="locations-title">CONVENIENT LOCATIONS</div>
    <div class="locations-line">RIVERTON 210-555-0143</div>
    <div class="locations-line">OAK FALLS 830-555-0187</div>
  </div>

  <div class="contact">
    <svg width="42" height="42" viewBox="0 0 42 42" fill="none" stroke="#1a1a1a" stroke-width="3.5"><circle cx="21" cy="21" r="18"/><ellipse cx="21" cy="21" rx="8" ry="18"/><line x1="3" y1="21" x2="39" y2="21"/><path d="M6 12h30M6 30h30"/></svg>
    <span>www.copperhollowstorage.com</span>
    <span class="divider">|</span>
    <svg width="48" height="34" viewBox="0 0 48 34"><rect x="1" y="1" width="46" height="32" fill="#1a1a1a"/><path d="M2 2l22 17 22-17M2 32l16-14M46 32l-16-14" fill="none" stroke="#fff" stroke-width="2.5"/></svg>
    <span>sales@copperhollowstorage.com</span>
  </div>
</article>
</body>
</html>
```